Zvo Klinieken website for a maxillofacial surgery clinic

It's a website for a clinic for maxillofacial surgery in WordPress . The website doesn't need to be complicated but has to look professional. It needs to be in Dutch so i can give the texts. Similar websites are www.tandartsenpraktijkveldorm.nl or www.pbtspecialisten.nl. Pages would be sort of similar to https://hetcentrumvoorgezichtszorg.nl/ or https://wervelmondclinics.nl/. Those lasts are maxillofacial surgery clinic websites, but there are little more extensive.
I uploaded the logo. If this is not the proper quality i can upload the eps. Logo was made through pixelforum.

Target Market(s)

Patients who can find me and see information about the clinic

Industry/Entity Type

Healthcare

Coding

Coded - Design and coding required

Number of Pages Required

5+ page

Font styles to use
Other font styles liked:
• Something standard professional

Colors
0054AA
0677BA
7BADD7
CADEEF
E8F1F8

Requirements
Nice to have
• Something in line with the logo. I prefer a little dark like the darker logos but I'm not sure if that's professional. Logos bkvzo and rlpw are instances i'm registered to so they will have to be on the website too but small somewhere.

```html
<!DOCTYPE html>
<html lang="nl">
<head>
<meta charset="utf-8">
<title>Zvo Klinieken</title>
<link href="https://fonts.googleapis.com/css2?family=Ubuntu:wght@400;500;700&family=Open+Sans:wght@300;400;600;700&display=swap" rel="stylesheet">
<style>
:root{
  --navy:#0a1d3f;
  --navy-2:#14264c;
  --blue:#2aa6e0;
  --heading:#2e3f5f;
  --text:#7a7f88;
  --light:#f2f4f7;
  --white:#fff;
}
*{box-sizing:border-box;margin:0;padding:0}
html,body{width:1200px;height:4177px;overflow:hidden}
body{position:relative;font-family:"Open Sans",sans-serif;color:var(--text);background:var(--white)}
.abs{position:absolute}
.h{font-family:"Ubuntu",sans-serif}
.ph{position:absolute}

/* header */
.topbar{left:390px;top:0;width:810px;height:32px;background:var(--navy-2);clip-path:polygon(20px 0,100% 0,100% 100%,0 100%)}
.topbar span{position:absolute;top:0;height:32px;line-height:32px;color:#fff;font-size:10px;font-weight:700;display:flex;align-items:center;gap:8px}
.topbar .appt{left:205px;width:232px;background:var(--blue);justify-content:center;text-transform:uppercase}
.navbar{left:0;top:32px;width:1200px;height:68px;background:#fff}
.brand{left:127px;top:40px;display:flex;align-items:center;gap:10px;font-family:"Ubuntu",sans-serif;font-size:26px;font-weight:500;color:var(--blue)}
.brand i{width:20px;height:20px;border-radius:50%;background:var(--blue);display:block}
.nav a{position:absolute;top:62px;font-size:11px;color:var(--heading);text-decoration:none}
.btn-contact{left:932px;top:54px;width:117px;height:29px;border:1.5px solid var(--heading);border-radius:3px;font-size:10px;font-weight:700;color:var(--heading);display:flex;align-items:center;justify-content:center}

/* hero */
.hero{left:0;top:100px;width:1200px;height:617px;background:linear-gradient(120deg,#3f4a5b 0%,#2b3446 40%,#4c5564 70%,#2b3241 100%)}
.badge{left:514px;top:300px;width:166px;height:34px;background:#2b3a5a;color:#fff;font-size:11px;font-weight:700;display:flex;align-items:center;justify-content:center}
.hero-title{left:0;width:1200px;top:348px;text-align:center;color:#fff;font-size:62px;font-weight:700;line-height:71px}
.btn-ghost{left:516px;top:517px;width:165px;height:46px;border:1.5px solid #fff;border-radius:3px;color:#fff;font-size:11px;font-weight:700;display:flex;align-items:center;justify-content:center}

/* about */
.diamond{width:170px;height:170px;transform:rotate(45deg);border:4px solid #fff}
.eyebrow{color:var(--blue);font-size:15px;font-weight:600}
.about-title{left:638px;top:858px;font-size:46px;font-weight:500;line-height:57px;color:var(--heading)}
.para{font-size:14px;line-height:24px;font-weight:300}
.btn-blue{background:var(--blue);color:#fff;font-family:"Ubuntu",sans-serif;font-size:16px;font-weight:500;display:flex;align-items:center;justify-content:center;gap:10px;border-radius:2px}

/* services */
.services{left:0;top:1359px;width:1200px;height:671px;background:var(--navy)}
.svc-img{top:1659px;width:320px;height:238px}
.svc-label{top:1868px;width:287px;height:78px;background:#fff;border-radius:4px;text-align:center}
.svc-label b{display:block;margin-top:14px;font-family:"Ubuntu",sans-serif;font-weight:500;font-size:18px;color:var(--heading)}
.svc-label small{display:block;margin-top:8px;font-size:12px;color:var(--text)}
.svc-icon{top:1602px;width:104px;height:104px}

/* values */
.values{left:0;top:2030px;width:1200px;height:592px;background:var(--light)}
.tab{top:2233px;height:45px;border-radius:3px;font-size:16px;display:flex;align-items:center;justify-content:center;background:#fff;color:var(--text);box-shadow:0 1px 4px rgba(0,0,0,.1)}
.check{display:flex;align-items:center;gap:10px;font-size:14px;font-weight:300}

/* contact */
.contact{left:0;top:2622px;width:1200px;height:436px;background:linear-gradient(90deg,#1c2d55,#2a3a66 60%,#233360)}
.field{left:692px;width:393px;height:46px;background:#4a5478;border-radius:5px;color:#fff;font-size:13px;font-weight:700;padding-left:52px;display:flex;align-items:center}

/* testimonials */
.t-photo{width:87px;height:121px}
.t-card{width:304px;height:162px;background:#fff;box-shadow:0 2px 12px rgba(0,0,0,.1);padding:32px 34px;font-size:13px;line-height:24px;font-weight:300}
.t-name{font-family:"Ubuntu",sans-serif;font-size:17px;font-weight:500;color:var(--heading)}
.t-city{font-size:12px;color:#a0a4ab}

/* footer */
.footer{left:0;top:3749px;width:1200px;height:428px;background:var(--navy)}
.f-head{font-family:"Ubuntu",sans-serif;font-size:19px;font-weight:500;color:#fff}
.f-small{font-size:12px;font-weight:700;color:#fff;line-height:25px}
.soc{top:4029px;width:29px;height:29px;background:#1e3159;border-radius:3px}
</style>
</head>
<body>

<!-- header -->
<div class="abs topbar">
  <span style="left:50px"><svg width="14" height="14" viewBox="0 0 24 24" fill="none" stroke="#fff" stroke-width="2"><path d="M22 16.9v3a2 2 0 0 1-2.2 2 19.8 19.8 0 0 1-8.6-3.1 19.5 19.5 0 0 1-6-6A19.8 19.8 0 0 1 2.1 4.2 2 2 0 0 1 4.1 2h3a2 2 0 0 1 2 1.7c.1 1 .4 1.9.7 2.8a2 2 0 0 1-.5 2.1L8 9.9a16 16 0 0 0 6 6l1.3-1.3a2 2 0 0 1 2.1-.5c.9.3 1.8.6 2.8.7a2 2 0 0 1 1.7 2z"/></svg>020 - 418 - 3307</span>
  <span class="appt"><svg width="16" height="14" viewBox="0 0 24 20" fill="none" stroke="#fff" stroke-width="2"><rect x="2" y="2" width="20" height="16" rx="1"/><path d="M2 3l10 8 10-8"/></svg>Request an appointment</span>
  <span style="left:470px"><svg width="12" height="14" viewBox="0 0 24 28" fill="none" stroke="#fff" stroke-width="2"><path d="M12 26s9-9 9-15a9 9 0 0 0-18 0c0 6 9 15 9 15z"/><circle cx="12" cy="11" r="3"/></svg>Kanaalweg 18 Rijswijk</span>
</div>
<div class="abs navbar"></div>
<div class="abs brand"><i></i>Zvo Klinieken</div>
<nav class="nav">
  <a style="left:366px">Thuis</a>
  <a style="left:456px">Behandelingen</a>
  <a style="left:590px">Vergoeding</a>
  <a style="left:697px">Ons team</a>
  <a style="left:789px">Folders</a>
</nav>
<div class="abs btn-contact">CONTACT US</div>

<!-- hero -->
<div class="abs hero" role="img" aria-label="Kaakchirurg met mondkapje behandelt een patiënt in de behandelkamer"></div>
<div class="abs badge">KAAKCHIRURGIE</div>
<h1 class="abs h hero-title">Precisiechirurgie,<br>Persoonlijke Zorg</h1>
<div class="abs btn-ghost">MEER LEREN</div>

<!-- about -->
<div class="abs diamond" style="left:252px;top:818px;background:linear-gradient(135deg,#9ab8d6,#3f6f9e)" role="img" aria-label="Tandartsteam met een lachend kind"></div>
<div class="abs diamond" style="left:129px;top:941px;background:linear-gradient(135deg,#d9b7a3,#3f7fb0)" role="img" aria-label="Vrouw bij tandheelkundig onderzoek"></div>
<div class="abs diamond" style="left:375px;top:941px;background:linear-gradient(135deg,#c9d6e2,#d7a98e)" role="img" aria-label="Lachende vrouw met spiegel"></div>
<div class="abs diamond" style="left:252px;top:1064px;background:linear-gradient(135deg,#e7d0b2,#8fb3d0)" role="img" aria-label="Lachend meisje in de tandartsstoel"></div>
<div class="abs" style="left:290px;top:1004px;width:94px;height:94px;border-radius:50%;background:#fff"></div>
<div class="abs" style="left:317px;top:1031px;width:40px;height:40px;border-radius:50%;background:var(--blue)"></div>

<div class="abs eyebrow h" style="left:640px;top:829px">Over Ons</div>
<h2 class="abs h about-title">Levens Kracht Geven,<br>Een Gezicht per Keer</h2>
<p class="abs para" style="left:640px;top:977px;width:455px">Lorem ipsum dolor sit amet, consectetur adipiscing elit, sed do eiusmod tempor incididunt ut labore et dolore magna aliqua. Ut enim ad minim veniam, quis nostrud exercitation ullamco laboris nisi ut aliquip ex ea commodo consequat. Duis aute irure dolor in reprehenderit in voluptate velit esse cillum dolore eu fugiat nulla pariatur. Excepteur sint occaecat cupidatat non proident, sunt in culpa qui officia deserunt mollit. ehenderit in voluptate velit esse cillum dolore eu fugiat nulla pariatur. Excepteur sint occaecat cupidatat non proident, sunt in culpa qui officia.</p>
<div class="abs btn-blue" style="left:640px;top:1216px;width:155px;height:46px">Meer Leren
  <svg width="18" height="14" viewBox="0 0 18 14" fill="none" stroke="#fff" stroke-width="2"><path d="M1 7h15M10 1l6 6-6 6"/></svg></div>

<!-- services -->
<div class="abs services"></div>
<div class="abs eyebrow h" style="left:0;width:1193px;text-align:center;top:1464px">Diensten</div>
<h2 class="abs h" style="left:0;width:1182px;text-align:center;top:1494px;font-size:46px;font-weight:500;color:#fff">Onze Diensten</h2>

<div class="abs svc-img" style="left:94px;background:linear-gradient(135deg,#e2e6ea,#9dbcd8 60%,#b5754a)" role="img" aria-label="Tandarts met mondkapje onderzoekt een patiënte"></div>
<div class="abs svc-img" style="left:441px;background:linear-gradient(135deg,#d7dde2,#c79a7e 55%,#3f86c0)" role="img" aria-label="Lachende patiënte met spiegel in de behandelstoel"></div>
<div class="abs svc-img" style="left:785px;background:linear-gradient(135deg,#c7d3de,#e6c6a8 55%,#a8b9c8)" role="img" aria-label="Lachend meisje bij de tandarts"></div>

<svg class="abs svc-icon" style="left:200px" viewBox="0 0 104 104"><path d="M2 52a50 50 0 0 1 100 0" fill="none" stroke="#fff" stroke-width="1.5"/><circle cx="52" cy="52" r="40" fill="var(--blue)"/><path d="M52 36l5 10 11 1-8 8 2 11-10-5-10 5 2-11-8-8 11-1z" fill="none" stroke="#fff" stroke-width="2"/></svg>
<svg class="abs svc-icon" style="left:547px" viewBox="0 0 104 104"><path d="M2 52a50 50 0 0 1 100 0" fill="none" stroke="#fff" stroke-width="1.5"/><circle cx="52" cy="52" r="40" fill="var(--blue)"/><circle cx="52" cy="54" r="15" fill="none" stroke="#fff" stroke-width="2"/><path d="M52 54l7-7" stroke="#fff" stroke-width="2"/></svg>
<svg class="abs svc-icon" style="left:893px" viewBox="0 0 104 104"><path d="M2 52a50 50 0 0 1 100 0" fill="none" stroke="#fff" stroke-width="1.5"/><circle cx="52" cy="52" r="40" fill="var(--blue)"/><path d="M40 66h24M46 60l10-22 6 3-10 22zM52 62a8 8 0 0 0 12-6" fill="none" stroke="#fff" stroke-width="2"/></svg>

<div class="abs svc-label" style="left:109px"><b>Kaakchirurgie</b><small>Read More &nbsp;›</small></div>
<div class="abs svc-label" style="left:455px"><b>Slaapgeneeskunde</b><small>Read More &nbsp;›</small></div>
<div class="abs svc-label" style="left:799px"><b>Plastische Chirurgie</b><small>Read More &nbsp;›</small></div>

<!-- values -->
<div class="abs values"></div>
<h2 class="abs h" style="left:105px;top:2118px;font-size:35px;font-weight:500;line-height:43px;color:var(--heading)">Symmetrie Vormgeven,<br>Harmonie Herstellen</h2>
<div class="abs tab h" style="left:105px;width:163px;background:var(--blue);color:#fff;font-weight:500">Kwaliteitsborging</div>
<div class="abs tab" style="left:282px;width:161px">Klantgericht</div>
<div class="abs tab" style="left:464px;width:149px">Professioneel</div>
<div class="abs" style="left:105px;top:2322px;width:223px;height:229px;background:linear-gradient(135deg,#4a8cc4,#d8a56a 60%,#c98a2c)" role="img" aria-label="Lachende patiënte in de behandelstoel"></div>
<p class="abs para" style="left:368px;top:2318px;width:325px">Lorem ipsum dolor sit amet, consectetur eiusmod tempor incididunt ut labore et dolore im ad minim veniam, quis nostrud exercitation eiusmod tempor incididunt ut labore et dolore im ad minim veniam, quis nostrud exercitation</p>
<div class="abs check" style="left:368px;top:2456px"><svg width="16" height="16" viewBox="0 0 16 16" fill="none" stroke="var(--blue)" stroke-width="1.5"><rect x="1" y="2" width="13" height="13"/><path d="M4 8l3 3 8-9"/></svg>Award winning company</div>
<div class="abs check" style="left:368px;top:2490px"><svg width="16" height="16" viewBox="0 0 16 16" fill="none" stroke="var(--blue)" stroke-width="1.5"><rect x="1" y="2" width="13" height="13"/><path d="M4 8l3 3 8-9"/></svg>Award winning company</div>
<div class="abs check" style="left:368px;top:2525px"><svg width="16" height="16" viewBox="0 0 16 16" fill="none" stroke="var(--blue)" stroke-width="1.5"><rect x="1" y="2" width="13" height="13"/><path d="M4 8l3 3 8-9"/></svg>Award winning company</div>
<div class="abs" style="left:786px;top:2079px;width:414px;height:543px;background:linear-gradient(160deg,#f2f4f7 0%,#aab4c2 35%,#2b2e38 75%,#1c1f27);clip-path:polygon(20% 20%,55% 8%,85% 0,100% 0,100% 100%,0 100%,4% 40%)" role="img" aria-label="Arts en collega bekijken samen een tablet"></div>

<!-- contact -->
<div class="abs contact" role="img" aria-label="Donkerblauwe sfeerfoto van de kliniek"></div>
<h2 class="abs h" style="left:109px;top:2762px;font-size:46px;font-weight:700;line-height:57px;color:#fff">Precisie bij Elke<br>Procedure, Perfectie<br>bij Elke Glimlach</h2>
<div class="abs h" style="left:692px;width:393px;text-align:center;top:2706px;font-size:21px;font-weight:500;color:#fff">Kom Met Ons In Contact</div>
<div class="abs field" style="top:2752px">Full Name</div>
<div class="abs field" style="top:2818px">Email Address</div>
<div class="abs field" style="top:2883px">Industry</div>
<div class="abs btn-blue" style="left:692px;top:2950px;width:393px;height:45px;border-radius:5px;font-family:'Open Sans',sans-serif;font-size:14px;font-weight:700">SUBMIT</div>

<!-- testimonials -->
<div class="abs eyebrow h" style="left:0;width:1203px;text-align:center;top:3147px">Getuigenissen</div>
<h2 class="abs h" style="left:0;width:1188px;text-align:center;top:3177px;font-size:46px;font-weight:500;color:var(--heading)">Wat Klanten Zeggen</h2>

<div class="abs t-photo" style="left:91px;top:3284px;background:linear-gradient(160deg,#cfd6dc,#3a4456)" role="img" aria-label="Portret van Pieter Vandam"></div>
<div class="abs t-name" style="left:203px;top:3306px">Pieter Vandam</div>
<div class="abs t-city" style="left:203px;top:3334px">Brussels</div>
<div class="abs t-card" style="left:110px;top:3389px">Lorem ipsum dolor sit amet, consect etur adipiscing elit, sed do eiusmod tempor incididunt ut labore et dolore magna aliqua. Ut enim ad minim veni am, quis nostrud</div>
<div class="abs h" style="left:356px;top:3352px;font-size:60px;font-weight:700;color:var(--blue);line-height:60px">&#8220;</div>

<div class="abs t-photo" style="left:438px;top:3284px;background:linear-gradient(160deg,#e3e5e7,#2a2d33)" role="img" aria-label="Portret van Lotte Bremer"></div>
<div class="abs t-name" style="left:545px;top:3306px">Lotte Bremer</div>
<div class="abs t-city" style="left:547px;top:3334px">Brussels</div>
<div class="abs t-card" style="left:458px;top:3389px">Lorem ipsum dolor sit amet, consect etur adipiscing elit, sed do eiusmod tempor incididunt ut labore et dolore magna aliqua. Ut enim ad minim veni am, quis nostrud</div>
<div class="abs h" style="left:703px;top:3352px;font-size:60px;font-weight:700;color:var(--blue);line-height:60px">&#8220;</div>

<div class="abs t-photo" style="left:787px;top:3284px;background:linear-gradient(160deg,#d9dde2,#6b87a6)" role="img" aria-label="Portret van Ruben Okafor"></div>
<div class="abs t-name" style="left:886px;top:3306px">Ruben Okafor</div>
<div class="abs t-city" style="left:888px;top:3334px">Brussels</div>
<div class="abs t-card" style="left:808px;top:3389px">Lorem ipsum dolor sit amet, consect etur adipiscing elit, sed do eiusmod tempor incididunt ut labore et dolore magna aliqua. Ut enim ad minim veni am, quis nostrud</div>
<div class="abs h" style="left:1052px;top:3352px;font-size:60px;font-weight:700;color:var(--blue);line-height:60px">&#8220;</div>

<div class="abs btn-blue" style="left:519px;top:3626px;width:156px;height:45px">Meer Leren
  <svg width="18" height="14" viewBox="0 0 18 14" fill="none" stroke="#fff" stroke-width="2"><path d="M1 7h15M10 1l6 6-6 6"/></svg></div>

<!-- footer -->
<div class="abs footer"></div>
<div class="abs" style="left:122px;top:3840px;display:flex;align-items:center;gap:12px;font-family:'Ubuntu',sans-serif;font-size:34px;font-weight:500;color:var(--blue)"><i style="width:26px;height:26px;border-radius:50%;background:var(--blue);display:block"></i>Zvo Klinieken</div>
<p class="abs f-small" style="left:113px;top:3932px;width:210px">Subscribe to our newsletter to recieve updates or the latest news</p>
<div class="abs soc" style="left:114px"></div>
<div class="abs soc" style="left:155px"></div>
<div class="abs soc" style="left:197px"></div>
<div class="abs soc" style="left:237px"></div>

<div class="abs f-head" style="left:517px;top:3853px">Newsletter</div>
<p class="abs f-small" style="left:517px;top:3901px;width:210px;font-size:11px">Subscribe to our newsletter to recieve updates or the latest news</p>
<div class="abs" style="left:517px;top:3993px;width:223px;height:40px;background:#2a3b60;border-radius:3px;color:#fff;font-size:11px;font-weight:600;display:flex;align-items:center;justify-content:space-between;padding:0 14px">Subscribe with us<svg width="9" height="14" viewBox="0 0 9 14" fill="none" stroke="#fff" stroke-width="2"><path d="M1 1l6 6-6 6"/></svg></div>

<div class="abs f-head" style="left:859px;top:3853px">Contacts</div>
<svg class="abs" style="left:862px;top:3902px" width="34" height="36" viewBox="0 0 34 36" fill="none" stroke="var(--blue)" stroke-width="1.5"><rect x="3" y="2" width="16" height="30" rx="3"/><path d="M9 28h4M23 12a6 6 0 0 1 0 10M27 9a10 10 0 0 1 0 16"/></svg>
<div class="abs" style="left:906px;top:3902px;font-family:'Ubuntu',sans-serif;font-size:17px;font-weight:500;color:#fff">Contact Us</div>
<div class="abs f-small" style="left:906px;top:3926px;font-weight:600">(31) 070-555-204</div>
<svg class="abs" style="left:862px;top:3972px" width="34" height="34" viewBox="0 0 34 34" fill="none" stroke="var(--blue)" stroke-width="1.5"><rect x="2" y="10" width="30" height="22"/><path d="M2 10l15 12 15-12M2 32l11-11M32 32L21 21M8 14V4h18v10"/></svg>
<div class="abs" style="left:906px;top:3973px;font-family:'Ubuntu',sans-serif;font-size:17px;font-weight:500;color:#fff">Contact Us</div>
<div class="abs f-small" style="left:906px;top:3997px;font-weight:600">(31) 070-555-204</div>

<div class="abs" style="left:0;top:4108px;width:1200px;height:1px;background:#1b2e54"></div>
<div class="abs" style="left:0;width:1222px;text-align:center;top:4144px;font-size:13px;font-weight:600;color:#fff">Zvo Klinieken</div>
<div class="abs" style="left:1064px;top:4137px;width:32px;height:34px;background:var(--blue);display:flex;align-items:center;justify-content:center"><svg width="14" height="9" viewBox="0 0 14 9" fill="none" stroke="#fff" stroke-width="2"><path d="M1 8l6-6 6 6"/></svg></div>

</body>
</html>
```